nutrition company business card

I would like to have a business card that has two sides, one being the green color from the Company name on the logo. I am open to ideas and looks that work with my logo. I like the idea of having a negative image of the tree on the green side.

For my information on the card I must have:
Megan Colbrook
415-555-0172
megancolbrook@quillpost.example

This area will need to be updated once I complete my schooling.

Reason: I need to extend my deadline by one day as I have been sick the last week and not had time to review all the new designs. Thank you.

Industry/Entity Type

Nutrition

Requirements
Must have
• I would like to have a business card that has two sides, one being the green color from the Company name on the logo. I am open to ideas and looks that work with my logo. I like the idea of having a negative image of the tree on the green side.
• For my information on the card I must have:
• Megan Colbrook
• 415-555-0172
• megancolbrook@quillpost.example
• This area will need to be updated once I complete my schooling.

```html
<!DOCTYPE html>
<html lang="en">
<head>
<meta charset="utf-8">
<title>Rooted Tables – Business Card</title>
<link rel="stylesheet" href="https://fonts.googleapis.com/css2?family=Quicksand:wght@300;400&family=Open+Sans:ital,wght@0,400;1,700&display=swap">
<style>
  :root {
    --brand-green: #7cc242;
    --brand-green-dark: #5e9e2c;
    --text-grey: #7d7d7d;
    --ink: #5a5a5a;
    --faint-grey: #e7e7e7;
    --card-white: #ffffff;
    --page-bg: #eeeae4;
  }
  * { box-sizing: border-box; margin: 0; padding: 0; }
  html, body {
    width: 1200px; height: 1024px; overflow: hidden;
    background: var(--page-bg);
  }
  .sheet {
    position: relative; width: 1200px; height: 1024px;
    display: flex; flex-direction: column; align-items: center;
    justify-content: center; gap: 64px;
  }
  .card {
    position: relative; width: 630px; height: 360px; overflow: hidden;
    box-shadow: 0 6px 18px rgba(0,0,0,0.12);
  }

  /* Front */
  .card--front { background: var(--card-white); }
  .card__watermark {
    position: absolute; right: -10px; top: -190px;
    width: 340px; height: 340px; border-radius: 50%;
    background: var(--faint-grey);
  }
  .brand {
    position: absolute; left: 44px; top: 118px;
    display: flex; align-items: center; gap: 16px;
  }
  .brand__mark {
    width: 66px; height: 66px; border-radius: 50%;
    border: 5px solid var(--brand-green);
  }
  .brand__name {
    font-family: "Quicksand", sans-serif; font-weight: 400;
    font-size: 34px; color: var(--brand-green); line-height: 1;
  }
  .brand__tagline {
    font-family: "Quicksand", sans-serif; font-weight: 400;
    font-size: 17px; color: var(--text-grey); letter-spacing: 0.5px;
    margin-top: 4px;
  }
  .contact {
    position: absolute; left: 124px; top: 222px;
    font-family: "Open Sans", sans-serif; color: var(--ink);
  }
  .contact__name {
    font-style: italic; font-weight: 700; font-size: 17px;
    color: var(--brand-green); margin-bottom: 6px;
  }
  .contact__line {
    display: flex; align-items: center; gap: 8px;
    font-size: 16px; line-height: 1.5;
  }
  .contact__icon { width: 14px; height: 14px; fill: var(--brand-green); }
  .card__edge {
    position: absolute; left: 0; right: 0; bottom: 0; height: 8px;
    background: var(--brand-green);
  }

  /* Back */
  .card--back {
    background: linear-gradient(135deg, var(--brand-green) 0%, #74b93c 100%);
    display: flex; flex-direction: column; align-items: center; justify-content: center;
    color: var(--card-white);
  }
  .back__mark {
    width: 104px; height: 104px; border-radius: 50%;
    border: 6px solid var(--card-white); margin-bottom: 22px;
  }
  .back__name {
    font-family: "Quicksand", sans-serif; font-weight: 400;
    font-size: 40px; line-height: 1;
  }
  .back__tagline {
    font-family: "Quicksand", sans-serif; font-weight: 400;
    font-size: 19px; letter-spacing: 0.6px; margin-top: 6px;
  }
</style>
</head>
<body>
<main class="sheet">
  <section class="card card--front" aria-label="Card front">
    <div class="card__watermark" aria-hidden="true"></div>
    <div class="brand">
      <div class="brand__mark" aria-hidden="true"></div>
      <div>
        <div class="brand__name">Rooted Tables</div>
        <div class="brand__tagline">healthy eating made easy</div>
      </div>
    </div>
    <div class="contact">
      <div class="contact__name">Megan Colbrook</div>
      <div class="contact__line">
        <svg class="contact__icon" viewBox="0 0 24 24" aria-hidden="true"><path d="M6.6 10.8a15.2 15.2 0 0 0 6.6 6.6l2.2-2.2a1 1 0 0 1 1-.25 11.4 11.4 0 0 0 3.6.57 1 1 0 0 1 1 1V20a1 1 0 0 1-1 1A17 17 0 0 1 3 4a1 1 0 0 1 1-1h3.5a1 1 0 0 1 1 1c0 1.25.2 2.45.57 3.57a1 1 0 0 1-.25 1z"/></svg>
        <span>415-555-0172</span>
      </div>
      <div class="contact__line">
        <svg class="contact__icon" viewBox="0 0 24 24" aria-hidden="true"><path d="M2 5h20v14H2z M3.5 6.5 12 13l8.5-6.5" fill="var(--brand-green)"/><path d="M3.5 6.5 12 13l8.5-6.5" fill="none" stroke="#fff" stroke-width="1.6"/></svg>
        <span>megancolbrook@quillpost.example</span>
      </div>
    </div>
    <div class="card__edge" aria-hidden="true"></div>
  </section>

  <section class="card card--back" aria-label="Card back">
    <div class="back__mark" aria-hidden="true"></div>
    <div class="back__name">Rooted Tables</div>
    <div class="back__tagline">healthy eating made easy</div>
  </section>
</main>
</body>
</html>
```